TL - business card

Tallow Partners is an insurance brokerage firm, inovative, proactive, vigorous, which aims to become the leader of the insurance brokers in Anfrica. We should like to get some designs which should be avoided also in Gray / Metallic for the Administration and Orange / Blue for the Managers (ike in the picture sent). The Blue / Green logo is not the correct one, but the source of the file. Please adjust the color accordingly for the business cards. 1 / Orange / Blue 2 / Gray / Metallic We want something classic but which is transmitted strenght, inovation, modernity and most of all, rapidity. We want something start-up like, very punchy and catching eye remaining profesional at the same time. Name: Dorian Whitlock Function: Managing Director Address: N ° 17/18 Rua Veloso - R / C 2B Direita - Bairro Mutamba - Luanda Tel: (+244) 947 582 316 Email: dorian.whitlock@tallow-p.example Website: www.tallow-p. example We want classic in the front and creative, colorfull at the back. The cards will be printed in relief, with very high quality of paper.
Insurance Broker
Colors
Designer to choose colors to be used in the design.

```html
<!DOCTYPE html>
<html lang="en">
<head>
<meta charset="utf-8">
<title>Tallow Partners – Business Card</title>
<link rel="stylesheet" href="https://fonts.googleapis.com/css2?family=Lato:wght@400;700&display=swap">
<style>
  :root {
    --blue: #1479bd;
    --orange: #e2781f;
    --white: #ffffff;
    --paper: #f4f4f4;
    --backdrop: #e6e7e9;
  }
  html, body {
    margin: 0;
    padding: 0;
    width: 1200px;
    height: 1021px;
    overflow: hidden;
    background: var(--backdrop);
    font-family: "Lato", sans-serif;
  }
  .card {
    position: absolute;
    left: 280px;
    width: 640px;
    height: 366px;
    overflow: hidden;
    box-shadow: 0 6px 18px rgba(0,0,0,0.18);
  }
  .card-front {
    top: 110px;
    background: var(--paper);
  }
  .card-back {
    top: 545px;
    background: var(--blue);
  }
  .brand {
    position: absolute;
    left: 0;
    right: 0;
    top: 120px;
    display: flex;
    align-items: center;
    justify-content: center;
    gap: 16px;
  }
  .brand-dot {
    width: 46px;
    height: 46px;
    border-radius: 50%;
    background: var(--orange);
  }
  .brand-name {
    font-weight: 700;
    font-size: 44px;
    color: var(--blue);
    letter-spacing: 1px;
  }
  .front-web {
    position: absolute;
    left: 0;
    right: 0;
    top: 236px;
    text-align: center;
    font-size: 20px;
    letter-spacing: 3px;
    color: var(--blue);
  }
  .back-circle {
    position: absolute;
    left: -150px;
    top: 40px;
    width: 420px;
    height: 420px;
    border-radius: 50%;
    border: 22px solid var(--orange);
    box-sizing: border-box;
  }
  .contact {
    position: absolute;
    right: 44px;
    top: 62px;
    text-align: right;
    color: var(--white);
  }
  .contact-name {
    font-weight: 700;
    font-size: 27px;
    margin: 0;
  }
  .contact-role {
    font-size: 20px;
    color: var(--orange);
    margin: 0 0 26px;
  }
  .contact-address {
    font-size: 19px;
    line-height: 1.3;
    margin: 0 0 14px;
    font-style: normal;
  }
  .contact-line {
    font-size: 19px;
    line-height: 1.32;
    display: flex;
    justify-content: flex-end;
    align-items: center;
    gap: 8px;
    margin: 0;
  }
  .contact-line svg {
    width: 18px;
    height: 18px;
    flex: none;
  }
</style>
</head>
<body>
  <section class="card card-front">
    <div class="brand">
      <span class="brand-dot"></span>
      <span class="brand-name">Tallow Partners</span>
    </div>
    <div class="front-web">www.tallow-p.example</div>
  </section>

  <section class="card card-back">
    <div class="back-circle"></div>
    <div class="contact">
      <p class="contact-name">Dorian Whitlock</p>
      <p class="contact-role">Managing Director</p>
      <address class="contact-address">
        N ° 17/18 Rua Veloso<br>
        R / C 2B Direita<br>
        Bairro Mutamba - Luanda
      </address>
      <p class="contact-line">(+244) 947 582 316
        <svg viewBox="0 0 24 24" aria-hidden="true"><path fill="#e2781f" d="M6.6 10.8a15 15 0 0 0 6.6 6.6l2.2-2.2c.3-.3.7-.4 1-.2 1.1.4 2.3.6 3.6.6.6 0 1 .4 1 1V20c0 .6-.4 1-1 1A17 17 0 0 1 3 4c0-.6.4-1 1-1h3.5c.6 0 1 .4 1 1 0 1.3.2 2.5.6 3.6.1.3 0 .7-.2 1z"/></svg>
      </p>
      <p class="contact-line">dorian.whitlock@tallow-p.example
        <svg viewBox="0 0 24 24" aria-hidden="true"><rect x="2.5" y="5" width="19" height="14" fill="none" stroke="#e2781f" stroke-width="2"/><path d="M3 6l9 7 9-7" fill="none" stroke="#e2781f" stroke-width="2"/></svg>
      </p>
      <p class="contact-line">www.tallow-p.example
        <svg viewBox="0 0 24 24" aria-hidden="true"><g fill="none" stroke="#e2781f" stroke-width="1.8"><circle cx="12" cy="12" r="9"/><ellipse cx="12" cy="12" rx="4" ry="9"/><path d="M3 12h18M5 7h14M5 17h14"/></g></svg>
      </p>
    </div>
  </section>
</body>
</html>
```